Cleaning service website design

We need a new nice web design(logo will be the same) for a new cleaning service Company:

Informations about Company and logo you can take from flyers in attachments.

This is a cleaning service Company which have simple rules and we would like to show that(in checklist form) on website:

- What we do and that we're Cleaning Green

- Why us?

- How much(our pricing is simple)

Also we would like to communicate with clients by some nice/big pictures on website and the most important thing is our phone number and short/fast Brimtallow.

Also there should be some space for description about our Company.

Generally all information on main page can be short: about us, about service(what we do), last reviews, tips (for example: Tip of the week) and other can be some introduction to subpage where will be more information.

There will be few subpages like: About us, About our service, Photos(Before and after), Reviews , Tips, FAQ, Contact, Looking for a Job? - most of them will be just text so you can project just one example.

```html
<!DOCTYPE html>
<html lang="en">
<head>
<meta charset="utf-8">
<title>Tidy Nest – House Cleaning</title>
<link href="https://fonts.googleapis.com/css2?family=Source+Sans+3:wght@400;600;700&display=swap" rel="stylesheet">
<style>
:root{
  --green:#6cb33f;
  --green-dark:#4f8f1f;
  --blue:#1a6fb5;
  --link-blue:#3aa6d6;
  --orange:#f58a07;
  --orange-light:#ffb020;
  --text:#7a7a7a;
  --text-dark:#333;
  --nav:#777;
  --topbar:#f4f4f4;
  --footer:#2b2b2b;
  --footer-bottom:#1b1b1b;
  --white:#fff;
}
*{margin:0;padding:0;box-sizing:border-box}
html,body{width:1082px;height:1200px;overflow:hidden}
body{position:relative;background:var(--white);font-family:"Source Sans 3",sans-serif;color:var(--text)}
a{text-decoration:none;color:inherit}
.abs{position:absolute}

.top-bar{left:0;top:0;width:1082px;height:29px;background:var(--topbar);border-bottom:1px solid #e6e6e6}
.account-links{right:136px;top:7px;font-size:12px;font-weight:600;color:#888}
.account-links span{margin:0 6px;color:#bbb}

.site-header{left:0;top:29px;width:1082px;height:98px;background:#f7f7f7}
.brand{left:135px;top:44px;display:flex;align-items:center;gap:10px}
.brand-dot{width:40px;height:40px;border-radius:50%;background:var(--green)}
.brand-name{font-size:26px;font-weight:700;color:var(--blue)}
.call-box{right:136px;top:40px;text-align:right}
.call-label{font-size:11px;font-weight:600;color:var(--blue)}
.call-label em{font-style:normal;color:var(--green)}
.call-number{font-size:25px;font-weight:700;color:var(--orange);line-height:1}
.main-nav{right:136px;top:96px;display:flex;gap:34px;font-size:11px;font-weight:600;color:var(--nav);letter-spacing:.2px}
.main-nav a.active{color:var(--green);border-bottom:2px solid var(--green);padding-bottom:3px}

.hero{left:135px;top:127px;width:811px;height:319px;background:linear-gradient(180deg,#6d9bd3 0%,#b5c3cf 35%,#9a9590 65%,#5d7a3a 100%)}
.hero-title{left:168px;top:178px;font-size:33px;font-weight:700;color:var(--white);line-height:1.15;text-shadow:0 2px 3px rgba(0,0,0,.35)}
.hero-sub{left:168px;top:273px;font-size:17px;font-weight:600;color:var(--white);text-shadow:0 1px 2px rgba(0,0,0,.4)}
.hero-sub strong{color:var(--orange)}
.quote-btn{left:168px;top:339px;width:222px;height:52px;display:flex;border-radius:4px;overflow:hidden;box-shadow:0 2px 4px rgba(0,0,0,.25)}
.quote-btn .label{flex:1;background:linear-gradient(#ffae1a,#f57f02);color:#5a2b00;font-size:15px;font-weight:700;display:flex;align-items:center;padding-left:25px}
.quote-btn .arrow{width:51px;background:linear-gradient(#fff,#e8e8e8);display:flex;align-items:center;justify-content:center}

.feature{top:492px;width:256px;height:167px;background:linear-gradient(135deg,#f6f6f6,#e9e9e9);border:1px solid #eee}
.feature h3{position:absolute;top:20px;width:100%;text-align:center;font-size:17px;font-weight:400;color:#8a8a8a}
.feature p{position:absolute;left:21px;top:52px;width:220px;font-size:11.5px;line-height:21px;color:#8a8a8a}
.feature .more-btn{position:absolute;left:21px;top:125px;width:54px;height:17px;background:linear-gradient(#6cbf22,#3e8e0f);color:var(--white);font-size:10px;font-weight:600;text-align:center;line-height:17px;border-radius:2px}
.feature .art{position:absolute;right:18px;bottom:10px;width:70px;height:80px;border-radius:8px}

.welcome{left:135px;top:712px;width:520px}
.section-title{font-size:21px;font-weight:400;color:#444}
.welcome p{margin-top:16px;font-size:12px;line-height:24.5px;color:var(--text)}
.read-more{display:block;margin-top:11px;font-size:11.5px;font-weight:600;color:var(--text-dark)}
.divider{left:680px;top:730px;width:1px;height:140px;background:linear-gradient(transparent,#e2e2e2,transparent)}
.press{left:722px;top:712px;width:225px}
.press h4{margin-top:16px;font-size:14px;font-weight:600;color:var(--link-blue)}
.press p{margin-top:8px;font-size:12px;line-height:23.5px;color:var(--text)}

.site-footer{left:0;top:951px;width:1082px;height:212px;background:var(--footer);color:var(--white)}
.footer-col{top:32px}
.footer-col h5{font-size:15px;font-weight:600;margin-bottom:10px}
.footer-col li{list-style:none;font-size:11px;font-weight:600;line-height:21px}
.footer-col p{font-size:11px;font-weight:600}
.newsletter-form{display:flex;gap:6px;margin-top:11px}
.newsletter-input{width:274px;height:36px;background:var(--white);border-radius:3px;color:#333;font-size:11px;font-weight:600;display:flex;align-items:center;padding-left:13px}
.go-btn{width:38px;height:36px;border-radius:3px;background:linear-gradient(var(--orange-light),var(--orange));font-size:12px;font-weight:700;display:flex;align-items:center;justify-content:center}
.social{display:flex;gap:9px;margin-top:32px}
.social span{width:20px;height:20px;border-radius:2px}
.footer-brand{right:136px;top:146px;display:flex;align-items:center;gap:7px}
.footer-brand .brand-dot{width:26px;height:26px}
.footer-brand .brand-name{font-size:18px;color:var(--green)}
.footer-bottom{left:0;top:1163px;width:1082px;height:37px;background:var(--footer-bottom)}
.copyright{left:135px;top:11px;font-size:11px;color:#555}
</style>
</head>
<body>

<div class="abs top-bar">
  <div class="abs account-links"><a href="#">Login</a><span>|</span><a href="#">Register</a></div>
</div>

<header class="abs site-header">
  <div class="abs brand" style="top:15px"><span class="brand-dot"></span><span class="brand-name">Tidy Nest</span></div>
  <div class="abs call-box" style="top:12px">
    <div class="call-label">CALL US FOR A <em>BRIMTALLOW</em></div>
    <div class="call-number">555-014-2290</div>
  </div>
  <nav class="abs main-nav" style="top:68px">
    <a class="active" href="#">HOME</a><a href="#">ABOUT US</a><a href="#">ABOUT OUR SERVICE</a><a href="#">PHOTOS</a><a href="#">REVIEWS</a><a href="#">TIPS</a><a href="#">FAQ</a><a href="#">CONTACT</a>
  </nav>
</header>

<div class="abs hero" role="img" aria-label="Photo of a smiling cleaning team with gloves and cleaning supplies in front of a house"></div>
<h1 class="abs hero-title">Affordably making your<br>life Simpler!</h1>
<p class="abs hero-sub">Imagine! House cleaning as&nbsp; low as <strong>$79</strong></p>
<a class="abs quote-btn" href="#"><span class="label">GET A FREE QUOTE</span><span class="arrow"><svg width="20" height="14" viewBox="0 0 20 14"><path d="M2 2l5 5-5 5M10 2l5 5-5 5" fill="none" stroke="#f58a07" stroke-width="2.4"/></svg></span></a>

<section class="abs feature" style="left:135px">
  <h3>What We Do</h3>
  <p>Lorem ipsum dolor sit amet consectetur adipiscing elit duis ante<br>is a dummy text.</p>
  <a class="more-btn" href="#">more</a>
  <div class="art" role="img" aria-label="Illustration of a bucket and spray bottle" style="background:linear-gradient(135deg,#6a5bd0,#2c8fd8)"></div>
</section>
<section class="abs feature" style="left:413px">
  <h3>Why Choose Us</h3>
  <p>Sed ut parspatisas ante dolore ut magna nisi, Aliquam vestibulum nabi<br>jane, mowla jane.</p>
  <a class="more-btn" href="#">more</a>
  <div class="art" role="img" aria-label="Illustration of a blue figure holding a window squeegee" style="width:45px;background:linear-gradient(#9fc9ef,#1f7fd0)"></div>
</section>
<section class="abs feature" style="left:690px">
  <h3>How Much Does It Cost</h3>
  <p>Aliquam magna nisi tortor ut aliquam elit ante dolore is a standard<br>dummy text.</p>
  <a class="more-btn" href="#">more</a>
  <div class="art" role="img" aria-label="Illustration of a money sack" style="background:radial-gradient(circle at 40% 40%,#e2d2a9,#a58c58)"></div>
</section>

<section class="abs welcome">
  <h2 class="section-title">Welcome to Tidynest.com</h2>
  <p>Lorem ipsum dolor sit amet consectetur adipiscing elit duis, ante dolore ut aliquam magna nisi is<br>a simply standard dummy text for the typesetting industry worldwide. You can add your own text<br>by replaceing this dummy text. Sed ut parspatisas ante dolore ut aliquam magna nisi is also a dummy<br>text for the typesetting industry.</p>
  <a class="read-more" href="#">Read more...</a>
</section>
<div class="abs divider"></div>
<section class="abs press">
  <h2 class="section-title">Press Releases</h2>
  <h4>Sed ut parspatisas ut dolore ante</h4>
  <p>Lorem ipsum dolor sit amet consectetur adi piscing elit duis. Sed ut parspatisas ut dolore ante. Magna consectetur vehicualm</p>
  <a class="read-more" href="#">View more...</a>
</section>

<footer class="abs site-footer">
  <div class="abs footer-col" style="left:134px"><h5>Quick Links</h5><ul><li>Home</li><li>About Us</li><li>About Our Service</li><li>Photos</li><li>Contact</li></ul></div>
  <div class="abs footer-col" style="left:297px"><h5>Useful Links</h5><ul><li>Terms of use</li><li>Privacy Policy</li><li>Help Center</li><li>Community</li><li>Login Area</li></ul></div>
  <div class="abs footer-col" style="left:443px"><h5>Join Our Community</h5><ul><li>Friendwall</li><li>Chirper</li><li>Linkhub</li></ul></div>
  <div class="abs footer-col" style="left:627px">
    <h5>SignUp For Our Monthly Newsletter</h5>
    <p>Subscribe our newsletter &amp; get the latest news &amp; updates</p>
    <div class="newsletter-form"><div class="newsletter-input">Email Address</div><div class="go-btn">GO</div></div>
    <div class="social"><span style="background:#2d5fb0"></span><span style="background:#3fb1e6"></span><span style="background:#f3b31b"></span></div>
  </div>
  <div class="abs footer-brand"><span class="brand-dot"></span><span class="brand-name">Tidy Nest</span></div>
</footer>
<div class="abs footer-bottom"><p class="abs copyright">© 2013 by, Tidy Nest. All Rights Reserved.</p></div>

</body>
</html>
```